New Wordpress Design Project - Australian native plant nursery

I'm Seeking a wordpress website with landing page with contact details and social links, that page will link to another 4 pages. I'm happy to just add in the information once the template is set up (draft text provided on word doc).
Needing pages of information pages for:
- Nursery, what we carry and that we provide garden design services, pictures of plants and gardens
- Native flowers & what we provide, flower arrangements for weddings, special occasions, pictures
- Giftwear short blurb that we carry local artisan giftwear, pictures
- about us with history of the nursery & pictures
* Also wanting a link for e-gift cards. The link will go to an external page (square) so I don’t need to set up the website for purchases.
Social media links
Social links
https://www.facebook.com/ThePebbleHollowGarden
https://www.instagram.com/thepebblehollowgardennursery

Two local native nursery websites that I like the style of:
https://www.brimbarkstemnursery.com.au/
https://www.telvoni.com.au/

I'm using two versions of our logo, we have the smaller circle and then the other logo which is stretched out. We have used the second design for our signs at the nursery, I've asked the sign guy for a copy of the design as I don't currently have one. I have vector files of the other design.

We have wordpress set up with elemantor and hosting with godaddy, I can send you the logon details once design is confirmed.

Target Market(s)

Anyone who likes gardening, we have a pretty even spread of customers across male/female and all ages

Industry/Entity Type

Garden centre with native plants, flowers and giftwear

Coding

Coded - Design and coding required

Colors
0054AA
0677BA
7BADD7
CADEEF
E8F1F8
0094D4
00A9DD
6FCCEA
C7EBF8
E9F6FB
00AB8E
00BBA5
67D7C9
C6EFE9
E9F9F6

Requirements
Must have
• Organic/modern/minimalist design
Nice to have
• Blue/white/green, flannel flowers as per logo

```html
<!DOCTYPE html>
<html lang="en">
<head>
<meta charset="utf-8">
<title>The Pebble Hollow Garden – Native Plant Nursery</title>
<link href="https://fonts.googleapis.com/css2?family=Prata&family=Roboto:wght@400;500;700&family=Lato:wght@400;700&display=swap" rel="stylesheet">
<style>
:root{
  --blue:#0054AA;
  --blue-mid:#0a5cc0;
  --blue-deep:#0649a0;
  --green:#00AB8E;
  --green-soft:#67D7C9;
  --green-pale:#E9F9F6;
  --ink:#333;
  --text:#555;
  --white:#fff;
  --serif:'Prata', serif;
  --sans:'Roboto', sans-serif;
}
*{margin:0;padding:0;box-sizing:border-box}
html,body{width:1200px;height:3504px;overflow:hidden}
body{position:relative;font-family:var(--sans);color:var(--text);background:var(--white)}
.abs{position:absolute}
a{color:inherit;text-decoration:none}

/* top bar */
.topbar{left:0;top:0;width:1200px;height:52px;background:var(--blue);color:var(--white);font-size:13px;font-weight:500}
.topbar .item{position:absolute;top:0;height:52px;display:flex;align-items:center;gap:10px}
.topbar .dot{color:#8fd13f;font-size:11px}
.social{position:absolute;top:12px;width:28px;height:28px;border-radius:50%}
.social.fb{left:311px;background:#3b5bb0}
.social.tw{left:345px;background:#1da1f2}
.social.gp{left:379px;background:#e0463a}

/* nav */
.navbar{left:0;top:52px;width:1200px;height:98px;background:var(--white)}
.nav{position:absolute;top:40px;right:112px;display:flex;gap:28px;font-size:13px;font-weight:700;color:#222;letter-spacing:.1px}
.nav .active{color:var(--green)}
.brand{left:104px;top:53px;width:212px;height:212px;border-radius:50%;background:var(--white);z-index:5;display:flex;align-items:center;justify-content:center}
.brand-name{width:150px;font-family:var(--serif);font-size:22px;line-height:1.25;color:#444;text-align:center}

/* hero */
.hero{left:0;top:150px;width:1200px;height:687px;background:
  radial-gradient(ellipse 300px 260px at 600px 420px,#8b7fd6 0%,#6f67b8 40%,rgba(60,70,60,0) 75%),
  linear-gradient(160deg,#7f9a4a 0%,#3e5a2a 35%,#2a2f2a 70%,#4a5a3a 100%)}
.hero-box{left:317px;top:348px;width:566px;height:193px;background:rgba(30,30,30,.55);text-align:center;color:var(--white)}
.hero-box h1{font-family:var(--serif);font-weight:400;font-size:44px;margin-top:25px;letter-spacing:.5px;white-space:nowrap;line-height:1.2}
.hero-box p{font-family:'Lato',sans-serif;font-size:17px;margin-top:6px}
.btn{display:inline-flex;align-items:center;justify-content:center;width:182px;height:46px;border-radius:23px;background:var(--green);color:var(--white);font-size:14px;font-weight:700;letter-spacing:.3px}
.hero-box .btn{margin-top:16px}
.hero-curve{left:0;top:737px;width:1200px;height:100px}

/* about */
.about{left:0;top:837px;width:1200px;text-align:center}
.eyebrow{font-family:var(--serif);color:var(--green);font-size:19px}
.title{font-family:var(--serif);font-weight:400;color:var(--blue);font-size:44px;line-height:1.2}
.rule{height:2px;width:96px;background:var(--blue)}
.about .title{margin-top:6px}
.about .rule{margin:14px auto 0;background:var(--green)}
.about p{width:830px;margin:22px auto 0;font-size:14.5px;line-height:21.5px;color:#666}
.about .btn{margin-top:18px}

/* what we do */
.services{left:0;top:1245px;width:1200px;height:642px;background:
  radial-gradient(circle at 1050px 80px,rgba(90,150,230,.5),rgba(0,0,0,0) 320px),
  radial-gradient(circle at 150px 550px,rgba(70,130,220,.35),rgba(0,0,0,0) 300px),
  linear-gradient(180deg,var(--blue-mid),var(--blue-deep))}
.services .title{position:absolute;left:112px;top:77px;color:var(--white)}
.services .rule{position:absolute;left:112px;top:150px;width:99px;background:var(--white)}
.services .lead{position:absolute;left:486px;top:80px;width:610px;color:var(--white);font-size:14.5px;line-height:21.5px}
.card{position:absolute;top:188px;width:311px;height:363px}
.card .photo{width:311px;height:288px}
.card .caption{position:absolute;left:0;bottom:0;width:311px;height:75px;background:var(--green);color:var(--white);font-weight:700;font-size:14px;line-height:22px;text-align:center;padding-top:15px}
.card.alt .caption,.card.alt .badge{background:var(--green-soft)}
.badge{position:absolute;left:103px;top:232px;width:104px;height:104px;border-radius:50%;background:var(--green);display:flex;justify-content:center;padding-top:16px}

/* giftwear */
.gift{left:0;top:1887px;width:1200px;height:644px}
.gift .title{position:absolute;left:110px;top:80px}
.gift .rule{position:absolute;left:112px;top:143px;width:99px}
.gift .copy{position:absolute;left:112px;top:170px;width:466px;font-size:14.5px;line-height:21.5px;text-align:justify;color:#666}
.gift .copy p+p{margin-top:22px}
.gift .btn{position:absolute;left:112px;top:488px}
.gift-ring{left:657px;top:105px;width:430px;height:430px;border-radius:50%;border:3px solid #555}
.gift-photo{left:672px;top:120px;width:400px;height:400px;border-radius:50%;background:radial-gradient(circle at 55% 40%,#c9b27a,#7a5a4a 45%,#4a4036 80%)}

/* native flowers */
.native{left:0;top:2531px;width:1200px;height:680px;background:var(--green);text-align:center}
.native .title{color:var(--white);margin-top:77px}
.native .rule{margin:12px auto 0;width:96px;background:var(--white)}
.flower{position:absolute;top:164px;width:300px;text-align:center}
.flower .disc{position:relative;width:300px;height:296px}
.flower .back{position:absolute;left:12px;top:8px;width:288px;height:288px;border-radius:50%;background:var(--blue)}
.flower .front{position:absolute;left:1px;top:0;width:288px;height:288px;border-radius:50%}
.flower h3{font-weight:400;font-size:18px;color:var(--white);line-height:26px;margin-top:32px}
.footer-curve{left:0;top:3085px;width:1200px;height:113px}

/* footer */
.footer{left:0;top:3197px;width:1200px;height:307px;background:var(--blue);color:var(--white)}
.contact{position:absolute;top:18px;width:300px;text-align:center}
.contact .icon{width:84px;height:84px;border-radius:50%;background:var(--white);border:3px solid var(--green);margin:0 auto;display:flex;align-items:center;justify-content:center;box-shadow:0 0 0 3px var(--white)}
.contact h4{color:var(--green);font-size:18px;font-weight:700;margin-top:17px}
.contact p{font-size:14.5px;line-height:21.5px;margin-top:4px}
.divider{position:absolute;top:11px;width:1px;height:212px;background:rgba(255,255,255,.3)}
.footer-line{position:absolute;left:112px;top:226px;width:976px;height:1px;background:rgba(255,255,255,.3)}
.copyright{position:absolute;left:0;top:253px;width:1200px;text-align:center;font-size:15px}
</style>
</head>
<body>

<header>
  <div class="abs topbar">
    <div class="item" style="left:112px"><span class="dot">●</span>Mon-Sat: 07:00 - 17:00</div>
    <a class="social fb" href="https://www.facebook.com/ThePebbleHollowGarden" aria-label="Facebook"></a>
    <span class="social tw" aria-label="Twitter"></span>
    <a class="social gp" href="https://www.instagram.com/thepebblehollowgardennursery" aria-label="Instagram"></a>
    <div class="item" style="left:692px">
      <svg width="14" height="11" viewBox="0 0 14 11"><rect x="0.5" y="0.5" width="13" height="10" rx="1" fill="#00AB8E"/><path d="M1 1l6 5 6-5" stroke="#0054AA" fill="none"/></svg>
      info@companyname.com</div>
    <div class="item" style="left:960px">
      <svg width="13" height="13" viewBox="0 0 24 24"><path fill="#00AB8E" d="M6.6 10.8a15 15 0 006.6 6.6l2.2-2.2a1 1 0 011-.25 11 11 0 003.6.6 1 1 0 011 1V20a1 1 0 01-1 1A17 17 0 013 4a1 1 0 011-1h3.5a1 1 0 011 1 11 11 0 00.6 3.6 1 1 0 01-.25 1z"/></svg>
      +1 888 888 8888</div>
  </div>

  <div class="abs navbar">
    <nav class="nav">
      <a class="active" href="#">HOME</a>
      <a href="#">ABOUT US</a>
      <a href="#">NURSERY</a>
      <a href="#">NATIVE FLOWERS</a>
      <a href="#">GIFTWEAR</a>
      <a href="#">CONTACT US</a>
    </nav>
  </div>

  <div class="abs brand">
    <span class="brand-name">The Pebble Hollow Garden</span>
  </div>
</header>

<section class="abs hero" role="img" aria-label="Close-up photo of purple native fan flowers in nursery pots"></section>
<div class="abs hero-box">
  <h1>PEBBLE HOLLOW</h1>
  <p>Welcome to our native plant nursery information page!</p>
  <a class="btn" href="#">GET STARTED</a>
</div>
<svg class="abs hero-curve" viewBox="0 0 1200 100" preserveAspectRatio="none">
  <path d="M0 100 Q600 0 1200 100 Z" fill="#00AB8E"/>
  <path d="M0 100 Q600 26 1200 100 Z" fill="#fff"/>
</svg>

<section class="abs about">
  <div class="eyebrow">ABOUT US</div>
  <h2 class="title">FLORAL SEASONS</h2>
  <div class="rule"></div>
  <p>Lorem ipsum dolor sit amet, consectetur adipiscing elit, sed do eiusmod tempor incididunt ut labore et dolore magna aliqua. Ut enim ad minim veniam, quis nostrud exercitation ullamco laboris nisi ut aliquip ex ea commodo consequat. Duis aute irure dolor in reprehenderit in voluptate velit esse cillum dolore eu fugiat nulla pariatur. Excepteur sint occaecat cupidatat non proident, sunt in culpa qui officia deserunt mollit anim id est laborum.Lorem ipsum dolor sit amet, consectetur adipiscing elit, sed do eiusmod tempor incididunt ut labore et dolore magna aliqua. Ut enim ad minim veniam, quis nostrud exercitation ullamco laboris nisi ut aliquip ex ea commodo consequat. Duis aute irure dolor in reprehenderit in voluptate velit esse cillum dolore eu fugiat nulla cupidatat non proident, sunt in culpa qui officia deserunt mollit anim id est laborum.</p>
  <a class="btn" href="#">LEARN MORE</a>
</section>

<section class="abs services">
  <h2 class="title">WHAT WE DO</h2>
  <div class="rule"></div>
  <p class="lead">Lorem ipsum dolor sit amet, consectetur adipiscing elit, sed do eiusmod tempor incididunt ut labore et dolore magna aliqua. Ut enim ad minim veniam, quis nostrud exercitation</p>

  <article class="card" style="left:112px">
    <div class="photo" role="img" aria-label="Photo of pink kangaroo paw flowers" style="background:radial-gradient(circle at 45% 40%,#e88aa0,#c75a78 45%,#4d6a3a 85%)"></div>
    <div class="badge"><svg width="48" height="44" viewBox="0 0 48 44" fill="none" stroke="#fff" stroke-width="2"><circle cx="24" cy="12" r="4"/><circle cx="24" cy="12" r="9"/><path d="M4 20v12l10 10M44 20v12L34 42M10 26l8 8h12l8-8"/></svg></div>
    <div class="caption">LOREM IPSUM DOLOR SIT AMET,<br>CONSECTETUR</div>
  </article>
  <article class="card alt" style="left:444px">
    <div class="photo" role="img" aria-label="Photo of white rice flower shrubs" style="background:radial-gradient(circle at 60% 65%,#e8ecd6,#9aa874 40%,#2f4a24 85%)"></div>
    <div class="badge"><svg width="48" height="44" viewBox="0 0 48 44" fill="none" stroke="#fff" stroke-width="2"><circle cx="20" cy="14" r="4"/><circle cx="20" cy="14" r="10"/><path d="M20 24v16M20 32q10-2 14-10M30 36h12"/></svg></div>
    <div class="caption">LOREM IPSUM DOLOR SIT AMET,<br>CONSECTETUR</div>
  </article>
  <article class="card" style="left:777px">
    <div class="photo" role="img" aria-label="Photo of a mixed native flower arrangement with banksia and protea" style="background:radial-gradient(circle at 60% 40%,#d8c890,#8a6a5a 40%,#5a3a4a 60%,#3e5a34 90%)"></div>
    <div class="badge"><svg width="52" height="44" viewBox="0 0 52 44" fill="none" stroke="#fff" stroke-width="2"><circle cx="14" cy="14" r="6"/><circle cx="38" cy="12" r="6"/><path d="M4 40q0-14 10-14t10 14M28 40q0-16 10-16t10 16"/></svg></div>
    <div class="caption">LOREM IPSUM DOLOR SIT AMET,<br>CONSECTETUR</div>
  </article>
</section>

<section class="abs gift">
  <h2 class="title">GIFTWEAR</h2>
  <div class="rule"></div>
  <div class="copy">
    <p>Lorem ipsum dolor sit amet, consectetur adipiscing elit, sed do eiusmod tempor incididunt ut labore et dolore magna aliqua. Ut enim ad minim veniam, quis nostrud exercitation ullamco laboris nisi ut aliquip ex ea commodo consequat. Duis aute irure dolor in reprehenderit in voluptate velit esse cillum dolore eu fugiat nulla pariatur.</p>
    <p>Excepteur sint occaecat cupidatat non proident, sunt in culpa qui officia deserunt mollit anim id est laborum. Lorem ipsum dolor sit amet, consectetur adipiscing elit, sed do eiusmod tempor incididunt ut labore et dolore magna aliqua. Ut enim ad minim veniam, quis nostrud exercitation ullamco laboris nisi ut aliquip ex ea commodo consequat. Duis aute irure dolor in reprehenderit in voluptate velit esse cillum dolore eu fugiat nulla pariatur. Excepteur sint occaecat cupidatat non proident, sunt in culpa qui officia deserunt mollit anim id est laborum.</p>
  </div>
  <a class="btn" href="#">LEARN MORE</a>
  <div class="abs gift-ring"></div>
  <div class="abs gift-photo" role="img" aria-label="Photo of a native flower arrangement with gum nuts in a stone vase"></div>
</section>

<section class="abs native">
  <h2 class="title">NATIVE FLOWERS</h2>
  <div class="rule"></div>
  <div class="flower" style="left:129px">
    <div class="disc"><div class="back"></div><div class="front" role="img" aria-label="Photo of the nursery shop front with painted flowers" style="background:radial-gradient(circle at 50% 30%,#c8c0b4,#7a5a44 45%,#4a3426 85%)"></div></div>
    <h3>Farm Made Bouquets</h3>
  </div>
  <div class="flower" style="left:453px">
    <div class="disc"><div class="back"></div><div class="front" role="img" aria-label="Photo of the nursery garden path and plants" style="background:radial-gradient(circle at 50% 30%,#9ec0e8,#6a7a54 45%,#3e4a2e 85%)"></div></div>
    <h3>Consumer Bunches</h3>
  </div>
  <div class="flower" style="left:777px">
    <div class="disc"><div class="back"></div><div class="front" role="img" aria-label="Photo of a colourful native flower bouquet" style="background:radial-gradient(circle at 50% 50%,#f0d8d8,#e08aa0 40%,#c8a040 70%,#6a7a4a 95%)"></div></div>
    <h3>Programs Tailored to fit<br>customer's retail program</h3>
  </div>
</section>
<svg class="abs footer-curve" viewBox="0 0 1200 113" preserveAspectRatio="none">
  <path d="M0 113 Q600 -14 1200 113 Z" fill="#fff"/>
  <path d="M0 113 Q600 14 1200 113 Z" fill="#0054AA"/>
</svg>

<footer class="abs footer">
  <div class="contact" style="left:123px">
    <div class="icon"><svg width="20" height="26" viewBox="0 0 20 26"><path fill="#0054AA" d="M10 0a10 10 0 00-10 10c0 7 10 16 10 16s10-9 10-16A10 10 0 0010 0zm0 14a4 4 0 110-8 4 4 0 010 8z"/></svg></div>
    <h4>Address :</h4>
    <p>123,Lorem ipsum dolor sit<br>consectetur</p>
  </div>
  <div class="divider" style="left:450px"></div>
  <div class="contact" style="left:450px">
    <div class="icon"><svg width="24" height="24" viewBox="0 0 24 24"><path fill="#0054AA" d="M6.6 10.8a15 15 0 006.6 6.6l2.2-2.2a1 1 0 011-.25 11 11 0 003.6.6 1 1 0 011 1V20a1 1 0 01-1 1A17 17 0 013 4a1 1 0 011-1h3.5a1 1 0 011 1 11 11 0 00.6 3.6 1 1 0 01-.25 1z"/></svg></div>
    <h4>Phone :</h4>
    <p>+1 888 888 8888</p>
  </div>
  <div class="divider" style="left:751px"></div>
  <div class="contact" style="left:775px">
    <div class="icon"><svg width="26" height="20" viewBox="0 0 26 20"><rect width="26" height="20" rx="2" fill="#0054AA"/><path d="M1 2l12 9 12-9" stroke="#fff" stroke-width="2" fill="none"/></svg></div>
    <h4>Email :</h4>
    <p>info@companyname.com</p>
  </div>
  <div class="footer-line"></div>
  <p class="copyright">© 2023 Company name &nbsp;| All Rights Reserved | Terms and Conditions</p>
</footer>

</body>
</html>
```